English and Spanish Language School Needs a Business Card

Need a business card design a startup company called Maribel Language School. The company will offer English and Spanish conversational level courses designed to make the learner feel comfortable with grammar and vocabulary. We would like to see a logo with some colour that should communicate learning, growth.

Target Market(s)

Consumers and businesses

Industry/Entity Type

Education

Contact Information for Business Card

TBD

Font styles to use
Serif

Requirements
Must have
• Include the following
• Logo
• Name
• Title
• Cellphone Number
• Office Phone number
• Email address
• Office Address

```html
<!DOCTYPE html>
<html lang="en">
<head>
<meta charset="utf-8">
<title>Maribel Language School – Business Card</title>
<link href="https://fonts.googleapis.com/css2?family=Montserrat:wght@400;500;600;800&display=swap" rel="stylesheet">
<style>
  :root {
    --stage: #3a3a3a;
    --card: #050505;
    --red: #d4202a;
    --teal: #0ea3ad;
  }
  * { box-sizing: border-box; margin: 0; padding: 0; }
  html, body { width: 1200px; height: 900px; overflow: hidden; }
  body {
    background: var(--stage);
    font-family: "Montserrat", sans-serif;
    position: relative;
  }
  .card {
    position: absolute;
    left: 250px;
    width: 700px;
    height: 400px;
    background: var(--card);
    border-radius: 22px;
    overflow: hidden;
  }
  .card-front { top: 30px; }
  .card-back { top: 470px; }

  /* Wordmark */
  .wordmark { color: var(--red); font-weight: 800; line-height: 1; }
  .wordmark-name { display: block; font-size: 96px; letter-spacing: -2px; }
  .wordmark-sub { display: block; font-size: 30px; letter-spacing: 0; margin-top: 4px; }

  .card-front .wordmark {
    position: absolute; left: 0; right: 0; top: 110px; text-align: center;
  }
  .front-web {
    position: absolute; left: 0; right: 0; bottom: 48px;
    text-align: center; font-size: 17px; font-weight: 500; color: var(--teal);
  }
  .front-web .accent { color: var(--red); }

  /* Back side */
  .band { position: absolute; left: 0; width: 62px; }
  .band-teal { top: 0; height: 196px; background: var(--teal); }
  .band-red { top: 204px; height: 196px; background: var(--red); }

  .card-back .wordmark { position: absolute; left: 100px; top: 58px; }
  .card-back .wordmark-name { font-size: 66px; letter-spacing: -1.5px; }
  .card-back .wordmark-sub { font-size: 21px; }

  .tab-red {
    position: absolute; right: 0; top: 78px; width: 34px; height: 44px;
    background: var(--red);
  }
  .person { position: absolute; right: 58px; top: 80px; text-align: right; }
  .person-name { font-size: 27px; font-weight: 600; color: var(--red); letter-spacing: 1px; }
  .person-title { font-size: 15px; color: var(--teal); margin-top: 2px; }

  .rule {
    position: absolute; left: 130px; right: 40px; top: 190px;
    height: 3px; background: var(--teal);
  }

  .address {
    position: absolute; right: 40px; top: 222px; text-align: right;
    font-size: 17px; line-height: 1.35; color: var(--teal);
  }

  .contacts { position: absolute; left: 110px; top: 252px; list-style: none; }
  .contacts li {
    display: flex; align-items: center; gap: 14px;
    font-size: 18px; line-height: 28px; color: var(--teal);
  }
  .contacts li.web { color: var(--red); font-weight: 600; }
  .contacts svg { width: 15px; height: 15px; flex: none; }
</style>
</head>
<body>

  <section class="card card-front">
    <div class="wordmark">
      <span class="wordmark-name">Maribel</span>
      <span class="wordmark-sub">Language School</span>
    </div>
    <p class="front-web"><span class="accent">www.</span>maribellanguageschool<span class="accent">.com</span></p>
  </section>

  <section class="card card-back">
    <div class="band band-teal"></div>
    <div class="band band-red"></div>

    <div class="wordmark">
      <span class="wordmark-name">Maribel</span>
      <span class="wordmark-sub">Language School</span>
    </div>

    <div class="tab-red"></div>
    <div class="person">
      <p class="person-name">Tomas Reyes</p>
      <p class="person-title">Director</p>
    </div>

    <div class="rule"></div>

    <p class="address">Po Box 218<br>Lindfield VIC 3920</p>

    <ul class="contacts">
      <li>
        <svg viewBox="0 0 16 16" fill="none" stroke="#d4202a" stroke-width="1.6"><rect x="4" y="1" width="8" height="14" rx="1.5"/><line x1="7" y1="12.5" x2="9" y2="12.5"/></svg>
        +331 4872-1093
      </li>
      <li>
        <svg viewBox="0 0 16 16" fill="#d4202a"><path d="M3 1.5l3 .5 1 3.5-2 1.2a9 9 0 0 0 4.3 4.3l1.2-2 3.5 1 .5 3c-.5 1-1.5 1.5-2.5 1.5C6.5 14.5 1.5 9.5 1.5 4c0-1 .5-2 1.5-2.5z"/></svg>
        +331 4870-2218
      </li>
      <li>
        <svg viewBox="0 0 16 16" fill="none" stroke="#d4202a" stroke-width="1.6"><rect x="1.5" y="3.5" width="13" height="9"/><polyline points="1.5,3.5 8,9 14.5,3.5"/></svg>
        hello@maribelschool.com
      </li>
      <li class="web">
        <svg viewBox="0 0 16 16" fill="none" stroke="#d4202a" stroke-width="1.5"><circle cx="8" cy="8" r="6.5"/><ellipse cx="8" cy="8" rx="2.8" ry="6.5"/><line x1="1.5" y1="8" x2="14.5" y2="8"/></svg>
        maribellanguageschool.com
      </li>
    </ul>
  </section>

</body>
</html>
```